KORV PTY LTD - Business Cards

Design a modern business card - using the attached Designs.
Same design as on the front, apart from the names/numbers/emails to be different.
We want the cards to be very glossy to stand out, do I think the simple black/white/metallic will be effective.
Both lots of details below:

Tom Wrenshaw
Director
tom_korv@nulvane.com
0438 274 093

Lewis Corbyn
Director
lewis_korv@nulvane.com
0419 385 642

Industry/Entity Type

Business

```html
<!DOCTYPE html>
<html lang="en">
<head>
<meta charset="utf-8">
<title>KORV PTY LTD – Business Cards</title>
<link href="https://fonts.googleapis.com/css2?family=Exo+2:wght@400;500;700&display=swap" rel="stylesheet">
<style>
  :root {
    --stage: #3a3c3f;
    --card-white: #f4f4f4;
    --card-dark: #34373b;
    --ink-light: #ffffff;
    --ink-dark: #34373b;
  }
  * { margin: 0; padding: 0; box-sizing: border-box; }
  html, body {
    width: 1200px; height: 1018px; overflow: hidden;
    background: var(--stage);
    font-family: "Exo 2", sans-serif;
  }
  .sheet {
    width: 1200px; height: 1018px;
    display: flex; align-items: center; justify-content: center; gap: 40px;
  }
  .card {
    position: relative; width: 540px; height: 309px;
    background: var(--card-white); overflow: hidden;
    box-shadow: 0 12px 30px rgba(0,0,0,.35);
  }
  .card-shapes { position: absolute; inset: 0; }
  .brand {
    position: absolute; display: flex; align-items: center; gap: 8px;
    font-weight: 700; font-size: 17px; letter-spacing: 1px; color: var(--ink-dark);
  }
  .brand-dot {
    width: 20px; height: 20px; border-radius: 50%; background: var(--card-dark);
  }
  .front .brand { left: 34px; top: 40px; }
  .back .brand { left: 60px; top: 56px; }

  .details {
    position: absolute; right: 22px; top: 124px; width: 250px;
    text-align: right; color: var(--ink-light);
  }
  .rule { height: 1px; background: var(--ink-light); margin-bottom: 10px; }
  .name { font-size: 21px; font-weight: 500; letter-spacing: 1px; line-height: 1; }
  .title { font-size: 12px; letter-spacing: 1.5px; margin-top: 5px; margin-bottom: 20px; }
  .contact {
    display: flex; justify-content: flex-end; align-items: center; gap: 6px;
    font-size: 10px; font-weight: 400; letter-spacing: .5px; height: 19px;
    white-space: nowrap;
  }
  .contact svg { width: 11px; height: 11px; flex: none; }

  .web-strip {
    position: absolute; right: 22px; top: 96px; width: 24px; height: 196px;
    background: var(--card-white);
    display: flex; align-items: center; justify-content: center;
  }
  .web-strip span {
    transform: rotate(-90deg); white-space: nowrap;
    font-size: 11px; letter-spacing: 1.5px; color: var(--ink-dark);
  }
</style>
</head>
<body>
<main class="sheet">

  <section class="card front" aria-label="Card front">
    <svg class="card-shapes" viewBox="0 0 540 309" aria-hidden="true">
      <defs>
        <linearGradient id="rim" x1="0" y1="0" x2="1" y2="1">
          <stop offset="0" stop-color="#f0f0f1"/>
          <stop offset=".5" stop-color="#9a9da1"/>
          <stop offset="1" stop-color="#d7d8da"/>
        </linearGradient>
      </defs>
      <path d="M540 104 H322 A114 114 0 0 0 208 218 V309 H540 Z" fill="url(#rim)"/>
      <path d="M540 110 H330 A112 112 0 0 0 218 222 V309 H540 Z" fill="var(--card-dark)"/>
    </svg>

    <div class="brand"><span class="brand-dot"></span>KORV PTY LTD</div>

    <div class="details">
      <div class="rule"></div>
      <div class="name">TOM WRENSHAW</div>
      <div class="title">DIRECTOR</div>
      <div class="contact">0438 274 093
        <svg viewBox="0 0 12 12"><circle cx="6" cy="6" r="5.4" fill="none" stroke="#fff"/><path d="M4 3.5 5 5 4.6 5.6 6.4 7.4 7 7 8.5 8 7.8 8.8C6 8.8 3.2 6 3.2 4.2Z" fill="#fff"/></svg></div>
      <div class="contact">tom_korv@nulvane.com
        <svg viewBox="0 0 12 12"><circle cx="6" cy="6" r="5.4" fill="none" stroke="#fff"/><rect x="3.2" y="4" width="5.6" height="4" fill="#fff"/><path d="M3.2 4 6 6.3 8.8 4" stroke="#34373b" stroke-width=".7" fill="none"/></svg></div>
      <div class="contact">www.korvpty.com.au
        <svg viewBox="0 0 12 12"><circle cx="6" cy="6" r="5.4" fill="none" stroke="#fff"/><circle cx="6" cy="6" r="2.8" fill="none" stroke="#fff" stroke-width=".8"/><path d="M3.2 6H8.8M6 3.2V8.8" stroke="#fff" stroke-width=".6"/></svg></div>
      <div class="contact">14 Harlow Road 3rd Building Street
        <svg viewBox="0 0 12 12"><circle cx="6" cy="6" r="5.4" fill="none" stroke="#fff"/><path d="M6 9.2 4 5.8A2.2 2.2 0 1 1 8 5.8Z" fill="#fff"/><circle cx="6" cy="4.9" r=".8" fill="#34373b"/></svg></div>
    </div>
  </section>

  <section class="card back" aria-label="Card back">
    <svg class="card-shapes" viewBox="0 0 540 309" aria-hidden="true">
      <rect width="540" height="309" fill="var(--card-dark)"/>
      <path d="M0 0 H330 V160 A120 120 0 0 1 210 280 H0 Z" fill="var(--card-white)"/>
    </svg>
    <div class="brand"><span class="brand-dot"></span>KORV PTY LTD</div>
    <div class="web-strip"><span>www.korvpty.com.au</span></div>
  </section>

</main>
</body>
</html>
```